I just need to get that same logo on the business card but with different word. “The Hinges Roadside and Rental”

Name: Marek T
Number: 4759028416
Email: thehingesroadside@brivomail.test

On the back, can we di just the logo and the hinges roadside and rental around it.

If possible a black card with the gold storefront type font that you used before, would be amazing. I attached the original logo just in case.

Target Market(s)

Roadside assistance

Industry/Entity Type

Repair/ roadside

Contact Information for Business Card

Name, email, phone number

Requirements
Must have
• Everything in description
Nice to have
• Nice big logo

```html
<!DOCTYPE html>
<html lang="en">
<head>
<meta charset="utf-8">
<title>The Hinges Roadside and Rental – Business Card</title>
<link href="https://fonts.googleapis.com/css2?family=Montserrat:wght@400;500;700;800&display=swap" rel="stylesheet">
<style>
  :root {
    --backdrop: #3a3a3c;
    --card-black: #1b1b1c;
    --card-front: #232324;
    --pattern-dark: #111112;
    --pattern-sheen: #3c3c3e;
    --watermark-tone: #2c2c2d;
    --gold: #c9a45c;
    --white: #f2f2f2;
  }
  * { margin: 0; padding: 0; box-sizing: border-box; }
  html, body {
    width: 1200px; height: 801px; overflow: hidden;
    background: var(--backdrop);
    font-family: "Montserrat", sans-serif;
  }
  .stage {
    position: relative; width: 1200px; height: 801px;
    display: flex; align-items: center; justify-content: center; gap: 40px;
  }
  .card {
    position: relative; width: 540px; height: 309px;
    border-radius: 4px; overflow: hidden;
    box-shadow: 0 14px 30px rgba(0,0,0,.45);
  }
  .card--back { background: var(--card-black); }
  .card--front { background: var(--card-front); }

  .pattern-field {
    position: absolute; inset: 0;
    background:
      radial-gradient(ellipse at 85% 10%, var(--pattern-sheen), transparent 55%),
      linear-gradient(135deg, var(--pattern-dark) 0%, #1e1e1f 55%, #2a2a2b 100%);
  }

  .brand {
    position: absolute; display: flex; flex-direction: column; align-items: flex-start;
    white-space: nowrap;
  }
  .brand__row { display: flex; align-items: center; gap: 12px; }
  .brand__square { background: var(--gold); flex: none; }
  .brand__name {
    color: var(--gold); font-weight: 800; letter-spacing: 1.5px; line-height: 1;
  }
  .brand__tagline {
    color: var(--white); font-weight: 500; letter-spacing: 2px; margin-top: 8px;
  }

  .card--back .brand {
    left: 50%; top: 50%; transform: translate(-50%, -50%);
  }
  .card--back .brand__square { width: 40px; height: 40px; }
  .card--back .brand__name { font-size: 40px; }
  .card--back .brand__tagline { font-size: 12px; padding-left: 54px; }

  .watermark-area {
    position: absolute; right: 44px; top: 40px; width: 180px; height: 160px;
    background: var(--watermark-tone); border-radius: 2px;
  }
  .card--front .brand { left: 38px; top: 40px; }
  .card--front .brand__square { width: 30px; height: 30px; }
  .card--front .brand__name { font-size: 30px; }
  .card--front .brand__tagline { font-size: 10px; margin-top: 6px; padding-left: 42px; }

  .contact-person { position: absolute; left: 38px; top: 150px; }
  .person__name { color: var(--gold); font-weight: 800; font-size: 20px; letter-spacing: 1.5px; }
  .person__role { color: var(--white); font-size: 12px; margin-top: 3px; }
  .person__rule { width: 150px; height: 1px; background: var(--gold); margin: 10px 0 12px; }
  .contact-list { list-style: none; }
  .contact-list li {
    display: flex; align-items: center; gap: 8px;
    color: var(--white); font-size: 12px; margin-bottom: 7px; white-space: nowrap;
  }
  .contact-list svg { width: 12px; height: 12px; fill: var(--gold); flex: none; }
</style>
</head>
<body>
<main class="stage">
  <section class="card card--back">
    <div class="pattern-field" role="img" aria-label="Repeating gloss brand-mark pattern across the black card"></div>
    <div class="brand">
      <div class="brand__row">
        <span class="brand__square"></span>
        <span class="brand__name">THE HINGES</span>
      </div>
      <span class="brand__tagline">ROADSIDE AND RENTAL</span>
    </div>
  </section>

  <section class="card card--front">
    <div class="watermark-area" role="img" aria-label="Large faint brand mark decoration"></div>
    <div class="brand">
      <div class="brand__row">
        <span class="brand__square"></span>
        <span class="brand__name">THE HINGES</span>
      </div>
      <span class="brand__tagline">ROADSIDE AND RENTAL</span>
    </div>
    <div class="contact-person">
      <p class="person__name">MAREK T</p>
      <p class="person__role">President</p>
      <div class="person__rule"></div>
      <ul class="contact-list">
        <li>
          <svg viewBox="0 0 24 24" aria-hidden="true"><path d="M6.6 10.8a15 15 0 0 0 6.6 6.6l2.2-2.2a1 1 0 0 1 1-.25 11.4 11.4 0 0 0 3.6.57 1 1 0 0 1 1 1V20a1 1 0 0 1-1 1A17 17 0 0 1 3 4a1 1 0 0 1 1-1h3.5a1 1 0 0 1 1 1c0 1.25.2 2.45.57 3.6a1 1 0 0 1-.25 1z"/></svg>
          4759028416
        </li>
        <li>
          <svg viewBox="0 0 24 24" aria-hidden="true"><path d="M2 5h20v14H2z M2 5l10 8 10-8" stroke="#232324" stroke-width="1.5"/></svg>
          thehingesroadside@brivomail.test
        </li>
      </ul>
    </div>
  </section>
</main>
</body>
</html>
```